Halberd Guard Services

Our Company is a security business which needs a cut edge design, the final product should have all relevant information and maintain a bold but modern and professional look.

Target Market(s)

A cut edge design which will attract any audience

Industry/Entity Type

Security

Contact Information for Business Card

HALBERD GUARD SERVICES

Gregor Lindqvist
Operations Manager
Phone: 0491 735 219

Email: info@halberdguard.com.au
Web: www.halberdguard.com.au

Requirements
Must have
• Must be double sided and contain all relevant information and the company logo.

```html
<!DOCTYPE html>
<html lang="en">
<head>
<meta charset="utf-8">
<title>Halberd Guard Services – Business Card</title>
<link rel="stylesheet" href="https://fonts.googleapis.com/css2?family=Russo+One&family=Arimo:wght@400;700&display=swap">
<style>
  :root {
    --bg: #e9ebec;
    --card-white: #ffffff;
    --card-shade: #eef0f1;
    --teal: #3f6068;
    --orange: #f0a030;
    --orange-deep: #e8901e;
    --ink: #1d1d1d;
    --muted: #3a3a3a;
  }
  * { box-sizing: border-box; margin: 0; padding: 0; }
  html, body { width: 1200px; height: 951px; overflow: hidden; }
  body { background: var(--bg); position: relative; font-family: "Arimo", Arial, sans-serif; }

  .card {
    position: absolute;
    width: 620px;
    height: 354px;
    border-radius: 22px;
    overflow: hidden;
    box-shadow: 0 14px 30px rgba(0,0,0,.18);
  }

  /* Front */
  .card-front {
    left: 110px; top: 70px;
    background: radial-gradient(ellipse at 55% 40%, var(--card-white) 0%, var(--card-white) 45%, var(--card-shade) 100%);
  }
  .front-brand {
    position: absolute; left: 0; right: 0; top: 120px;
    display: flex; align-items: center; justify-content: center; gap: 16px;
  }
  .brand-dot { width: 46px; height: 46px; border-radius: 50%; background: var(--teal); flex: none; }
  .brand-name {
    font-family: "Russo One", "Arimo", sans-serif;
    color: var(--teal);
    font-size: 50px; letter-spacing: 1px; line-height: 1;
    white-space: nowrap;
  }
  .front-web {
    position: absolute; left: 0; right: 0; top: 262px; text-align: center;
    font-size: 20px; letter-spacing: 2px; color: var(--muted);
  }

  /* Back */
  .card-back { left: 470px; top: 520px; background: var(--card-white); }
  .back-shapes { position: absolute; inset: 0; }
  .back-brand {
    position: absolute; left: 46px; top: 68px;
    display: flex; align-items: center; gap: 10px;
  }
  .back-brand .brand-dot { width: 24px; height: 24px; }
  .back-brand .brand-name { font-size: 24px; }

  .contact-list { position: absolute; left: 40px; top: 158px; list-style: none; }
  .contact-list li {
    display: flex; align-items: flex-start; gap: 10px;
    font-size: 18px; line-height: 22px; color: var(--ink); margin-bottom: 6px;
  }
  .contact-list svg { flex: none; width: 16px; height: 16px; margin-top: 3px; fill: var(--orange); }
  .web-accent { color: var(--orange-deep); }

  .holder {
    position: absolute; left: 412px; width: 196px; top: 150px; text-align: center; color: #fff;
  }
  .holder-name { font-size: 22px; font-weight: 700; letter-spacing: .3px; white-space: nowrap; }
  .holder-role { font-size: 16px; margin-top: 4px; }
</style>
</head>
<body>

<section class="card card-front" aria-label="Business card front">
  <div class="front-brand">
    <span class="brand-dot"></span>
    <span class="brand-name">HALBERD GUARD</span>
  </div>
  <p class="front-web">www.halberdguard.com.au</p>
</section>

<section class="card card-back" aria-label="Business card back">
  <svg class="back-shapes" viewBox="0 0 620 354" preserveAspectRatio="none" aria-hidden="true">
    <path d="M372 0 C346 110 350 240 392 354 L620 354 L620 0 Z" fill="var(--teal)"/>
    <path d="M398 0 C374 110 378 240 416 354 L620 354 L620 0 Z" fill="#ffffff"/>
    <path d="M404 0 C380 110 384 240 422 354 L620 354 L620 0 Z" fill="var(--orange)"/>
  </svg>

  <div class="back-brand">
    <span class="brand-dot"></span>
    <span class="brand-name">HALBERD GUARD</span>
  </div>

  <ul class="contact-list">
    <li>
      <svg viewBox="0 0 16 16"><path d="M8 1 L15 8 H13 V15 H10 V10 H6 V15 H3 V8 H1 Z"/></svg>
      <span>48 Rampart Lane<br>Brookvale, NSW 2100</span>
    </li>
    <li>
      <svg viewBox="0 0 16 16"><path d="M4 1 L7 4 L5 6 C6 8.5 7.5 10 10 11 L12 9 L15 12 L12.5 15 C6.5 14 2 9.5 1 3.5 Z"/></svg>
      <span>0491 735 219</span>
    </li>
    <li>
      <svg viewBox="0 0 16 16"><path d="M4 2 H11 V6 H4 Z M1 7 H15 V13 H1 Z M4 10 H12 V15 H4 Z"/></svg>
      <span>0491 735 220</span>
    </li>
    <li>
      <svg viewBox="0 0 16 16"><path d="M1 3 H15 V13 H1 Z M1 3 L8 9 L15 3" stroke="#fff" stroke-width="1"/></svg>
      <span>info@halberdguard.com.au</span>
    </li>
    <li>
      <svg viewBox="0 0 16 16"><circle cx="8" cy="8" r="7"/></svg>
      <span>www.<span class="web-accent">halberdguard</span>.com.au</span>
    </li>
  </ul>

  <div class="holder">
    <p class="holder-name">Gregor Lindqvist</p>
    <p class="holder-role">Operations Manager</p>
  </div>
</section>

</body>
</html>
```